TL - business card

Tallow Partners is an insurance brokerage firm, inovative, proactive, vigorous, which aims to become the leader of the insurance brokers in Anfrica. We should like to get some designs which should be avoided also in Gray / Metallic for the Administration and Orange / Blue for the Managers (ike in the picture sent). The Blue / Green logo is not the correct one, but the source of the file. Please adjust the color accordingly for the business cards. 1 / Orange / Blue 2 / Gray / Metallic We want something classic but which is transmitted strenght, inovation, modernity and most of all, rapidity. We want something start-up like, very punchy and catching eye remaining profesional at the same time. Name: Dorian Whitlock Function: Managing Director Address: N ° 17/18 Rua Veloso - R / C 2B Direita - Bairro Mutamba - Luanda Tel: (+244) 947 582 316 Email: dorian.whitlock@tallow-p.example Website: www.tallow-p. example We want classic in the front and creative, colorfull at the back. The cards will be printed in relief, with very high quality of paper.
Insurance Broker
Colors
Designer to choose colors to be used in the design.

```html
<!DOCTYPE html>
<html lang="en">
<head>
<meta charset="utf-8">
<title>Tallow Partners – Business Card</title>
<link rel="stylesheet" href="https://fonts.googleapis.com/css2?family=Exo+2:wght@600;700&family=Lato:wght@400;700&display=swap">
<style>
  :root {
    --orange: #ea6a26;
    --blue: #2ea6dc;
    --ink: #4a4a4a;
    --rule: #cfcfcf;
    --paper: #ffffff;
    --stage: #2e2e2e;
    --watermark: #f1f1f1;
  }
  * { margin: 0; padding: 0; box-sizing: border-box; }
  html, body { width: 1200px; height: 866px; overflow: hidden; background: var(--stage); }
  .canvas {
    width: 1200px; height: 866px;
    display: flex; flex-direction: column; align-items: center; justify-content: center; gap: 44px;
  }
  .card {
    position: relative; width: 640px; height: 366px; overflow: hidden;
    box-shadow: 0 14px 30px rgba(0,0,0,.45);
  }

  /* Front */
  .card-front { background: var(--paper); font-family: "Lato", sans-serif; color: var(--ink); }
  .card-front .watermark {
    position: absolute; left: 80px; top: 20px; width: 300px; height: 300px;
    border-radius: 50%; border: 26px solid var(--watermark);
  }
  .identity { position: absolute; left: 38px; top: 78px; }
  .person-name {
    font-family: "Exo 2", sans-serif; font-weight: 600; font-size: 25px;
    letter-spacing: .5px; text-transform: uppercase; line-height: 1;
  }
  .person-name .first { color: var(--orange); }
  .person-name .last { color: var(--blue); }
  .person-role { font-size: 16px; margin-top: 4px; }
  .contact { list-style: none; margin-top: 10px; font-size: 16px; }
  .contact li { display: flex; align-items: center; gap: 7px; line-height: 1.45; }
  .contact svg { width: 15px; height: 15px; flex: none; }
  .divider { position: absolute; left: 300px; top: 132px; width: 305px; height: 1px; background: var(--rule); }
  .brand {
    position: absolute; right: 34px; top: 72px; display: flex; align-items: center; gap: 12px;
  }
  .brand-name {
    font-family: "Exo 2", sans-serif; font-weight: 700; font-size: 27px;
    letter-spacing: 1px; text-transform: uppercase; color: var(--blue);
  }
  .brand-mark { width: 46px; height: 46px; border-radius: 50%; border: 6px solid var(--orange); }
  .address {
    position: absolute; right: 36px; top: 200px; text-align: right;
    font-size: 16px; line-height: 1.4; letter-spacing: .3px;
  }
  .address-rule { position: absolute; left: 300px; top: 268px; width: 305px; height: 1px; background: var(--rule); }
  .edge-band { position: absolute; left: 0; right: 0; bottom: 0; height: 12px; display: flex; }
  .edge-band .warm { width: 52%; background: var(--orange); }
  .edge-band .cool { flex: 1; background: var(--blue); }

  /* Back */
  .card-back {
    background: linear-gradient(20deg, var(--orange) 0%, #d8733f 38%, #6f9cc0 68%, var(--blue) 100%);
    display: flex; align-items: center; justify-content: center;
  }
  .card-back .brand { position: static; }
  .card-back .brand-name { color: var(--paper); font-size: 34px; }
  .card-back .brand-mark { width: 60px; height: 60px; border-color: var(--paper); border-width: 7px; }
</style>
</head>
<body>
<main class="canvas">
  <section class="card card-front" aria-label="Business card front">
    <div class="watermark"></div>
    <div class="identity">
      <h1 class="person-name"><span class="first">Dorian</span> <span class="last">Whitlock</span></h1>
      <p class="person-role">Managing Director</p>
      <ul class="contact">
        <li>
          <svg viewBox="0 0 16 16" aria-hidden="true"><path fill="var(--orange)" d="M2 4c0-1 1-2 2-2h8c1 0 2 1 2 2v1h-3V4H5v1H2zM3 6h10l1 7H2zM8 8a2 2 0 1 0 0 4 2 2 0 0 0 0-4z"/></svg>
          (+244) 947 582 316
        </li>
        <li>
          <svg viewBox="0 0 16 16" aria-hidden="true"><rect x="1" y="3" width="14" height="10" fill="var(--orange)"/><path d="M1 3l7 6 7-6" fill="none" stroke="#fff" stroke-width="1.4"/></svg>
          dorian.whitlock@tallow-p.example
        </li>
      </ul>
    </div>
    <div class="divider"></div>
    <div class="brand">
      <span class="brand-name">Tallow Partners</span>
      <span class="brand-mark"></span>
    </div>
    <address class="address" style="font-style:normal">
      N ° 17/18 Rua Veloso - R / C<br>
      2B Direita<br>
      Bairro Mutamba - Luanda
    </address>
    <div class="address-rule"></div>
    <div class="edge-band"><span class="warm"></span><span class="cool"></span></div>
  </section>

  <section class="card card-back" aria-label="Business card back">
    <div class="brand">
      <span class="brand-mark"></span>
      <span class="brand-name">Tallow Partners</span>
    </div>
  </section>
</main>
</body>
</html>
```